Luxury Wine Label for New Startup Winery

We need a wine label for our new winery startup. We have worked with a local designer but do not feel the resulting label / logo have the elevation required to present our brand as a luxury wine. Our winery is called "Quailbrook Vineyards" and we are focused on extremely high quality hand crafted artisan and estate wines from the Pacific Northwest.
We would like to see designs that utilize a tree line, or other imagery that represents the "Quailbrook" part of our company name. Another interesting feature could be wood grain.
A logo will be required based on your design so please design with this in mind:
This logo should be consistent with the wine bottle label design, and should be representative of our high end exclusive wine while giving a sense of place (Oregon/ Pacific Northwest.)
I will supply an image of the design we received from our local designer, PLEASE NOTE: in general we do like wood grain and tree line concepts but feel the execution was poorly done.
ATTN: Logo design should be suitable for use on: Bottles (Red wine/rose/white wine), Bussiness cards, vehicle signage, business signage, etc
P.S.:
If you have a design that is not outside the box we are still interested in seeing it.
Label is for a burgundy style bottle with a label height of 3.5 - 4" and a width of 3.5-4"
any label <= 4"x4" and >=3.5"x3.5" will be acceptable:
HOWEVER Width should be greater than or equal to height due to the bottle format
Target Market(s)
Wine enthusiasts with adequate discretionary budgets to afford $100 bottles of wine.
Industry/Entity Type
Wine / Winery
Requirements
Must have
- A sense of luxury, a feel of exclusivity, and a theme consistent with our product and brand name
Nice to have
- Tree line, wood grain or other wood themes. Serif fonts
Should not have
- anything cheesy, off topic, hard to read script fonts or anything that makes the label hard to read from a few feet away or too busy

```html
<!DOCTYPE html>
<html lang="en">
<head>
<meta charset="UTF-8">
<title>Quailbrook Vineyards – Syrah Label</title>
<link href="https://fonts.googleapis.com/css2?family=Josefin+Sans:wght@400;600;700&display=swap" rel="stylesheet">
<style>
  :root {
    --page-bg: #e6e6e6;
    --gold: #c49a2c;
    --gold-dark: #a57f1e;
    --wood-light: #f1f1ef;
    --wood-mid: #dcdcd9;
    --ink: #1f1f1f;
  }
  html, body {
    margin: 0;
    padding: 0;
    width: 1200px;
    height: 1200px;
    overflow: hidden;
    background: var(--page-bg);
    font-family: "Josefin Sans", sans-serif;
  }
  .label {
    position: absolute;
    left: 100px;
    top: 115px;
    width: 1000px;
    height: 970px;
    box-sizing: border-box;
    border-radius: 44px;
    background: var(--gold);
    padding: 18px;
  }
  .label-panel {
    position: relative;
    width: 100%;
    height: 100%;
    border-radius: 30px;
    overflow: hidden;
    background: linear-gradient(100deg, var(--wood-mid) 0%, var(--wood-light) 30%, #e6e6e3 55%, var(--wood-light) 80%, var(--wood-mid) 100%);
  }
  .brand-mark {
    position: absolute;
    left: 50%;
    top: 50px;
    width: 130px;
    height: 130px;
    margin-left: -65px;
    background: var(--gold);
  }
  .text-line {
    position: absolute;
    left: 0;
    right: 0;
    margin: 0;
    text-align: center;
    line-height: 1;
  }
  .brand-name {
    top: 225px;
    font-size: 64px;
    font-weight: 600;
    letter-spacing: 4px;
    color: var(--gold);
  }
  .brand-sub {
    top: 300px;
    font-size: 36px;
    font-weight: 400;
    letter-spacing: 12px;
    color: var(--ink);
  }
  .varietal {
    top: 420px;
    font-size: 158px;
    font-weight: 600;
    letter-spacing: 34px;
    padding-left: 34px;
    color: var(--ink);
  }
  .appellation {
    top: 700px;
    font-size: 44px;
    font-weight: 600;
    letter-spacing: 3px;
    color: var(--gold-dark);
  }
  .vintage {
    top: 765px;
    font-size: 44px;
    font-weight: 600;
    letter-spacing: 5px;
    color: var(--gold-dark);
  }
</style>
</head>
<body>
  <div class="label">
    <div class="label-panel" role="img" aria-label="Whitewashed wood plank grain background">
      <div class="brand-mark"></div>
      <p class="text-line brand-name">QUAILBROOK</p>
      <p class="text-line brand-sub">VINEYARDS</p>
      <p class="text-line varietal">SYRAH</p>
      <p class="text-line appellation">WILLAMETTE VALLEY</p>
      <p class="text-line vintage">2024</p>
    </div>
  </div>
</body>
</html>
```